Woman owned consulting company needs an elegant and modern business card design

I need a business card design for my new consulting company, Mara Quillon Consulting. I am looking for something that is simple and elegant, but also creative and original. You can use either version of the logo that are attached. I have also included the information that needs to be featured on the business card.

Contact Information for Business Card

Requirements
Must have
• The logo and the font type and a standard business card size. Use shades of gray/silver and or rose gold that are in the logo.
• I didn't realize that my actual logo wasn't attached. Please incorporate in the designs.
Should not have
• Colors that are different from my logo

```html
<!DOCTYPE html>
<html lang="en">
<head>
<meta charset="utf-8">
<title>Mara Quillon Consulting — Business Card</title>
<link rel="stylesheet" href="https://fonts.googleapis.com/css2?family=Cinzel:wght@400;700&family=Lora:wght@400&display=swap">
<style>
  :root {
    --backdrop: #c9c9c9;
    --card: #f7f7f6;
    --silver: #9a9a9a;
    --charcoal: #3b3f41;
    --ink: #1f1f1f;
    --band-text: #f2f2f2;
  }
  * { margin: 0; padding: 0; box-sizing: border-box; }
  html, body { width: 1200px; height: 852px; overflow: hidden; }
  body {
    background: var(--backdrop);
    display: flex;
    align-items: center;
    justify-content: center;
    gap: 50px;
  }
  .card {
    position: relative;
    width: 500px;
    height: 286px;
    background: var(--card);
    border-radius: 16px;
    overflow: hidden;
    box-shadow: 0 6px 18px rgba(0,0,0,0.18);
  }
  .wordmark {
    position: absolute;
    font-family: "Cinzel", serif;
    font-weight: 400;
    color: var(--silver);
    letter-spacing: 1.5px;
    line-height: 1.05;
  }
  .card-back .wordmark { left: 0; right: 0; top: 92px; text-align: center; font-size: 30px; }
  .card-back .website {
    position: absolute;
    left: 0; right: 0; top: 178px;
    text-align: center;
    font-family: "Lora", serif;
    font-size: 12px;
    color: var(--ink);
  }
  .card-front .wordmark { left: 36px; top: 48px; font-size: 27px; }
  .person { position: absolute; left: 36px; top: 190px; }
  .person-name {
    font-family: "Cinzel", serif;
    font-weight: 700;
    font-size: 19px;
    letter-spacing: 1px;
    color: var(--ink);
  }
  .person-role {
    font-family: "Lora", serif;
    font-size: 12px;
    color: var(--ink);
    margin-top: 2px;
  }
  .contact-list {
    position: absolute;
    left: 262px; top: 132px;
    list-style: none;
    font-family: "Lora", serif;
    font-size: 11px;
    color: var(--ink);
  }
  .contact-list li { display: flex; align-items: center; gap: 8px; height: 17px; }
  .contact-list svg { width: 10px; height: 10px; fill: var(--charcoal); flex: none; }
  .company-band {
    position: absolute;
    left: 215px; right: 0; bottom: 0;
    height: 48px;
    background: var(--charcoal);
    border-top-left-radius: 14px;
    display: flex;
    align-items: center;
    justify-content: center;
    font-family: "Cinzel", serif;
    font-size: 13px;
    letter-spacing: 0.8px;
    color: var(--band-text);
  }
</style>
</head>
<body>
  <section class="card card-back">
    <div class="wordmark">Mara Quillon<br>Consulting, LLC</div>
    <div class="website">www.maraquillonconsulting.com</div>
  </section>

  <section class="card card-front">
    <div class="wordmark">Mara Quillon<br>Consulting, LLC</div>
    <ul class="contact-list">
      <li>
        <svg viewBox="0 0 10 10"><path d="M1 2.5 C1 1.5 2 1 5 1 C8 1 9 1.5 9 2.5 L9 3.5 L7 3.5 L7 2.6 L3 2.6 L3 3.5 L1 3.5 Z M2 5 L3.5 3.8 L6.5 3.8 L8 5 L8 9 L2 9 Z"/></svg>
        555-014-2273
      </li>
      <li>
        <svg viewBox="0 0 10 10"><path d="M0.5 2 H9.5 V8 H0.5 Z M0.5 2 L5 5.5 L9.5 2" fill="none" stroke="#3b3f41" stroke-width="1"/></svg>
        mara@maraquillonconsulting.com
      </li>
      <li>
        <svg viewBox="0 0 10 10"><circle cx="5" cy="5" r="4.3" fill="none" stroke="#3b3f41" stroke-width="1"/><ellipse cx="5" cy="5" rx="1.8" ry="4.3" fill="none" stroke="#3b3f41" stroke-width="0.8"/><path d="M0.7 5 H9.3" stroke="#3b3f41" stroke-width="0.8"/></svg>
        www.maraquillonconsulting.com
      </li>
    </ul>
    <div class="person">
      <div class="person-name">Mara Quillon</div>
      <div class="person-role">Owner</div>
    </div>
    <div class="company-band">Mara Quillon Consulting, LLC</div>
  </section>
</body>
</html>
```